Business Card Design for Marketing Firm

Looking for business card design for higher end marketing firm. Clean but impressionable/trendy. We are a marketing firm that represents manufacturers in the foodservice equipment and supply industry. Our customers are end users such has hotels, restaurants, country clubs, convention centers and casinos as well as distributors of restaurants supplies and equipment, and manufacturers of foodservice equipment and supplies.
Target Market(s)
Hotels, Restaurants, Supply & Equipment Distributors, Foodservice Manufacturers
Industry/Entity Type
Foodservice/Hospitality
Contact Information for Business Card
Name, Title, Contact Number, Email, Website, Social Media, Address
Requirements
Must have
- Clean & Simple but Serious and Impressionable

```html
<!DOCTYPE html>
<html lang="en">
<head>
<meta charset="utf-8">
<title>Meridian Hospitality Reps – Business Cards</title>
<link href="https://fonts.googleapis.com/css2?family=Open+Sans:wght@400;700&display=swap" rel="stylesheet">
<style>
  :root {
    --navy: #272a78;
    --ink: #1f1f2e;
    --paper: #ffffff;
    --backdrop: #e6e4e2;
  }
  * { box-sizing: border-box; margin: 0; padding: 0; }
  html, body { width: 1200px; height: 786px; overflow: hidden; }
  body {
    background: var(--backdrop);
    display: flex;
    align-items: center;
    justify-content: center;
    gap: 40px;
    font-family: "Open Sans", sans-serif;
  }
  .card {
    position: relative;
    width: 540px;
    height: 310px;
    background: var(--paper);
    box-shadow: 0 10px 30px rgba(0,0,0,.18);
    overflow: hidden;
  }
  .card-back { border-bottom: 6px solid var(--navy); }

  .card-band { position: absolute; left: 0; bottom: 0; width: 540px; height: 60px; display: block; }

  /* brand name: one colour, one weight, with a plain circle */
  .brand {
    display: flex;
    flex-direction: column;
    align-items: center;
    color: var(--navy);
  }
  .brand-dot { display: block; border-radius: 50%; background: var(--navy); }
  .brand-name {
    font-family: "Open Sans", sans-serif;
    font-weight: 700;
    line-height: 1.2;
    white-space: nowrap;
  }

  .front-brand { position: absolute; left: 20px; top: 92px; width: 265px; }
  .front-brand .brand-dot { width: 52px; height: 52px; margin-bottom: 16px; }
  .front-brand .brand-name { font-size: 16px; }

  .divider {
    position: absolute; left: 300px; top: 60px;
    width: 1.5px; height: 170px; background: var(--navy);
  }

  .contact {
    position: absolute; left: 322px; top: 58px;
    color: var(--ink); font-size: 12.5px; line-height: 1.45;
  }
  .contact-name { color: var(--navy); font-weight: 700; font-size: 19px; line-height: 1.1; }
  .contact-title { font-size: 12.5px; margin-bottom: 10px; }
  .contact-list { list-style: none; margin-bottom: 12px; }
  .contact-list li { display: flex; align-items: center; gap: 7px; }
  .contact-list svg { width: 12px; height: 12px; fill: var(--navy); flex: none; }
  .contact-address { font-style: normal; }

  .back-brand { position: absolute; left: 0; right: 0; top: 78px; }
  .back-brand .brand-dot { width: 68px; height: 68px; margin-bottom: 20px; }
  .back-brand .brand-name { font-size: 25px; }

  .social { display: flex; gap: 4px; margin-top: 16px; list-style: none; }
  .social li { width: 13px; height: 13px; border-radius: 50%; background: var(--navy); }
</style>
</head>
<body>

  <section class="card card-front" aria-label="Business card front">
    <div class="front-brand brand">
      <span class="brand-dot" aria-hidden="true"></span>
      <span class="brand-name">Meridian Hospitality Reps</span>
    </div>

    <div class="divider" aria-hidden="true"></div>

    <div class="contact">
      <p class="contact-name">DANIEL REED</p>
      <p class="contact-title">Managing Director</p>
      <ul class="contact-list">
        <li><svg viewBox="0 0 24 24" aria-hidden="true"><path d="M6.6 10.8a15 15 0 0 0 6.6 6.6l2.2-2.2c.3-.3.7-.4 1-.2 1.1.4 2.3.6 3.6.6.6 0 1 .4 1 1V20c0 .6-.4 1-1 1A17 17 0 0 1 3 4c0-.6.4-1 1-1h3.5c.6 0 1 .4 1 1 0 1.3.2 2.5.6 3.6.1.3 0 .7-.2 1z"/></svg>123 456 789</li>
        <li><svg viewBox="0 0 24 24" aria-hidden="true"><path d="M2 5h20v14H2zm2 2v.5l8 5 8-5V7zm0 2.8V17h16V9.8l-8 5z"/></svg>info@meridianreps.com</li>
        <li><svg viewBox="0 0 24 24" aria-hidden="true"><path d="M12 2a10 10 0 1 0 0 20 10 10 0 0 0 0-20zm0 2c.8 1.2 1.5 2.5 1.9 4h-3.8c.4-1.5 1.1-2.8 1.9-4zM4.3 14a8 8 0 0 1 0-4h3.4a16 16 0 0 0 0 4zm5.4 0a14 14 0 0 1 0-4h4.6a14 14 0 0 1 0 4zm6.6 0a16 16 0 0 0 0-4h3.4a8 8 0 0 1 0 4zM12 20c-.8-1.2-1.5-2.5-1.9-4h3.8c-.4 1.5-1.1 2.8-1.9 4z"/></svg>www.meridianreps.com</li>
      </ul>
      <address class="contact-address">Your address, City<br>State, Zip 1234</address>
    </div>

    <svg class="card-band" viewBox="0 0 540 60" aria-hidden="true">
      <polygon points="0,46 260,46 251,60 0,60" fill="var(--navy)"/>
      <polygon points="290,22 540,22 540,60 266,60" fill="var(--navy)"/>
    </svg>
  </section>

  <section class="card card-back" aria-label="Business card back">
    <div class="back-brand brand">
      <span class="brand-dot" aria-hidden="true"></span>
      <span class="brand-name">Meridian Hospitality Reps</span>
      <ul class="social" aria-label="Social media">
        <li></li><li></li><li></li><li></li><li></li><li></li>
      </ul>
    </div>
  </section>

</body>
</html>
```